Veltra Metrics New Website for Health Benefits Plan Decisioneering Tool Launch

Veltra Metrics is a SaaS provider of health benefits comparison tools. We need a new simple SaaS focused website to direct customers to our product

Target Market(s)

General Public comparing their health benefits plans from their employer or from the state exchanges in the US

Coding

Coded - Design and coding required

Number of Pages Required

3 page

Requirements
Must have
• Main page - "Know the Best Health Benefits Plan for You!"
Graphic of a person looking over papers on their desk
Compare Now button to link to SaaS product
About Us
Product Page

https://plimbo.example/top-app-pages/

```html
<!DOCTYPE html>
<html lang="en">
<head>
<meta charset="utf-8">
<title>Veltra Metrics – Health Benefits Plan Decisioneering</title>
<link href="https://fonts.googleapis.com/css2?family=Noto+Serif:wght@400;700&family=Arimo:wght@400&display=swap" rel="stylesheet">
<style>
:root{
  --blue:#2a93d5;
  --blue-dark:#1f7fc0;
  --ink:#333333;
  --body:#444444;
  --muted:#666666;
  --grey-band:#f1f1f3;
  --footer:#222222;
  --white:#ffffff;
  --line:#cfcfcf;
}
*{box-sizing:border-box;margin:0;padding:0}
html,body{width:1200px;height:3726px;overflow:hidden}
body{position:relative;background:var(--white);font-family:"Arimo",Arial,sans-serif;color:var(--body)}
.serif{font-family:"Noto Serif",Georgia,serif}
.abs{position:absolute}

/* header */
.site-header{position:absolute;left:0;top:0;width:1200px;height:129px;background:var(--white)}
.brand{position:absolute;left:113px;top:38px;font-family:"Noto Serif",Georgia,serif;font-size:31px;color:var(--blue);letter-spacing:.5px}
.main-nav{position:absolute;top:58px;left:0;width:1200px;font-family:"Noto Serif",Georgia,serif;font-size:14px;color:var(--ink)}
.main-nav span{position:absolute;white-space:nowrap}
.main-nav .active{color:var(--blue)}

/* hero */
.hero{position:absolute;left:0;top:129px;width:1200px;height:666px;
  background:linear-gradient(115deg,#5d6a76 0%,#8d959c 30%,#c9ccd0 55%,#9aa4ad 80%,#6a7a8a 100%)}
.hero-panel{position:absolute;left:656px;top:208px;width:486px;height:288px;background:rgba(40,40,40,.72)}
.hero-title{position:absolute;left:27px;top:17px;font-family:"Noto Serif",Georgia,serif;font-size:36px;color:var(--white);letter-spacing:.5px}
.hero-sub{position:absolute;left:27px;top:80px;font-family:"Noto Serif",Georgia,serif;font-size:30px;line-height:50px;color:var(--white)}
.hero-sub b{font-weight:700}
.btn-solid{position:absolute;display:flex;align-items:center;justify-content:center;border-radius:32px;
  background:linear-gradient(#3aa4e6,#1f86c8);color:var(--white);font-family:"Noto Serif",Georgia,serif}
.hero .btn-solid{left:26px;top:201px;width:185px;height:59px;font-size:19px}

/* welcome */
.section-title{position:absolute;left:0;width:1200px;text-align:center;font-family:"Noto Serif",Georgia,serif;color:var(--ink)}
.section-title em{font-style:normal;color:var(--blue)}
.rule{position:absolute;left:580px;width:40px;height:3px;background:var(--blue)}
.intro{position:absolute;left:270px;top:938px;width:660px;text-align:center;font-size:13px;line-height:28px;color:var(--body)}

.card{position:absolute;top:1086px;width:311px;height:306px;background:var(--white);
  box-shadow:0 2px 12px rgba(0,0,0,.12);text-align:center}
.card svg{position:absolute;left:115px;top:50px}
.card h3{position:absolute;top:140px;width:100%;font-family:"Noto Serif",Georgia,serif;font-weight:400;font-size:22px;color:var(--ink)}
.card p{position:absolute;top:185px;left:28px;width:255px;font-size:13px;line-height:28px;color:var(--body)}

/* features */
.features{position:absolute;left:0;top:1478px;width:1200px;height:932px;background:var(--grey-band)}
.feature-title{position:absolute;font-family:"Noto Serif",Georgia,serif;font-size:24px;line-height:40px;color:var(--ink)}
.feature-text{position:absolute;font-size:13px;line-height:27.5px;color:var(--body)}
.btn-outline{position:absolute;display:flex;align-items:center;justify-content:center;border:1.5px solid var(--blue);
  border-radius:30px;color:var(--blue);font-family:"Noto Serif",Georgia,serif;font-size:18px;background:transparent}
.illustration{position:absolute;border-radius:20px}

/* launch */
.launch{position:absolute;left:0;top:2410px;width:1200px;height:513px;background:var(--blue)}
.device{position:absolute;left:195px;top:48px;width:256px;height:465px;border-radius:40px 40px 0 0;
  background:linear-gradient(#eef2f5,#dfe5ea)}
.launch-kicker{position:absolute;left:529px;top:110px;font-family:"Noto Serif",Georgia,serif;font-size:27px;color:var(--white)}
.launch-title{position:absolute;left:529px;top:155px;font-family:"Noto Serif",Georgia,serif;font-size:34px;color:var(--white)}
.launch-text{position:absolute;left:533px;top:230px;width:456px;font-size:13px;line-height:25.5px;color:var(--white);text-align:justify}
.launch .btn-outline{left:533px;top:378px;width:178px;height:62px;border-color:var(--white);color:var(--white);font-size:19px}

/* contact */
.field{position:absolute;border:1px solid var(--line);background:var(--white);font-size:13px;color:var(--muted);padding:15px 15px}
.submit{left:519px;top:3307px;width:159px;height:54px;font-size:17px;font-family:"Noto Serif",Georgia,serif}

/* footer */
.site-footer{position:absolute;left:0;top:3402px;width:1200px;height:324px;background:var(--footer);color:var(--white)}
.footer-brand{position:absolute;left:0;top:48px;width:1200px;text-align:center;font-family:"Noto Serif",Georgia,serif;font-size:32px;letter-spacing:.5px}
.footer-nav{position:absolute;left:0;top:148px;width:1200px;text-align:center;font-family:"Noto Serif",Georgia,serif;font-size:15px}
.footer-nav span{margin:0 24px}
.social{position:absolute;left:495px;top:200px;display:flex;gap:7px}
.social i{display:block;width:36px;height:36px;border:1.5px solid var(--white);border-radius:50%}
.copyright{position:absolute;left:0;top:266px;width:1200px;text-align:center;font-family:"Noto Serif",Georgia,serif;font-size:15px}
</style>
</head>
<body>

<header class="site-header">
  <div class="brand">Veltra Metrics</div>
  <nav class="main-nav">
    <span class="active" style="left:646px">HOME</span>
    <span style="left:742px">ABOUT US</span>
    <span style="left:866px">PRODUCT</span>
    <span style="left:989px">CONTACT US</span>
  </nav>
</header>

<section class="hero" role="img" aria-label="Photo of a person at a desk with a laptop, reviewing printed charts and papers">
  <div class="hero-panel">
    <div class="hero-title">VELTRA METRICS</div>
    <div class="hero-sub">Know the <b>Best Health Benefits</b><br>Plan for You!</div>
    <a class="btn-solid">Compare Now</a>
  </div>
</section>

<h2 class="section-title" style="top:850px;font-size:37px;font-weight:400">Welocome to <em>Veltra Metrics</em></h2>
<div class="rule" style="top:912px"></div>
<p class="intro">Sed ut perspiciatis unde omnis iste natus error sit voluptatem accusantium doloremque laudantium, totam rem aperiam, eaque ipsa quae ab illo inventore veritatis et quasi architecto beatae vitae dicta sunt sit vol uptatem accusantium doloremque explicabo.</p>

<article class="card" style="left:111px">
  <svg width="82" height="62" viewBox="0 0 82 62" fill="none" stroke="#2a93d5" stroke-width="2.5">
    <rect x="2" y="2" width="78" height="50"/><path d="M30 60h22M41 52v8"/>
    <path d="M14 42V30M21 42V24M28 42V20M35 42V28"/><circle cx="60" cy="18" r="9"/><path d="M60 18V9M60 18h9M48 34h22M48 40h22"/>
  </svg>
  <h3>Services 01</h3>
  <p>Sed ut perspiciatis unde omnis iste natus error sit voluptatem accusantium dolorem que laudantium, totam rem</p>
</article>
<article class="card" style="left:444px">
  <svg width="82" height="78" viewBox="0 0 82 78" fill="none" stroke="#2a93d5" stroke-width="2.5">
    <path d="M42 60H2V2h62v34"/><path d="M2 14h62M8 22v30"/><circle cx="50" cy="8" r="1.5"/><circle cx="57" cy="8" r="1.5"/>
    <circle cx="60" cy="58" r="9"/><path d="M60 42v6M60 68v6M44 58h6M70 58h6M49 47l4 4M67 65l4 4M71 47l-4 4M53 65l-4 4"/>
  </svg>
  <h3>Services 02</h3>
  <p>Sed ut perspiciatis unde omnis iste natus error sit voluptatem accusantium dolorem que laudantium, totam rem</p>
</article>
<article class="card" style="left:776px">
  <svg width="82" height="80" viewBox="0 0 82 80" fill="none" stroke="#2a93d5" stroke-width="2.5">
    <path d="M6 48h12v28H6zM26 40h12v36H26zM46 50h12v26H46zM64 34h12v42H64z"/>
    <circle cx="10" cy="28" r="5"/><circle cx="30" cy="14" r="5"/><circle cx="52" cy="26" r="5"/><circle cx="72" cy="6" r="5"/>
    <path d="M14 25l12-8M35 16l13 8M56 22l12-12"/>
  </svg>
  <h3>Services 03</h3>
  <p>Sed ut perspiciatis unde omnis iste natus error sit voluptatem accusantium dolorem que laudantium, totam rem</p>
</article>

<section class="features">
  <h3 class="feature-title" style="left:135px;top:98px;font-weight:400">Sed ut perspiciatis unde omnis iste<br>natus error sit voluptatem</h3>
  <p class="feature-text" style="left:138px;top:196px;width:405px">Nemo enim ipsam voluptatem quia voluptas sit aspernatur aut odit aut fugit, sed quia consequuntur magni dolores eos qui ratione vol uptatem sequi nescemo enim ipsam voluptatem quia voluptas sit aspernatur aut odit aut fugit, sed quia consequuntur</p>
  <a class="btn-outline" style="left:140px;top:341px;width:163px;height:55px">Learn More</a>
  <div class="illustration" role="img" aria-label="Flat illustration of two people working at a large dashboard screen with charts" style="left:580px;top:60px;width:490px;height:370px;background:linear-gradient(135deg,#dfe6f3,#c9d5ec 60%,#e6d3dc)"></div>

  <div class="illustration" role="img" aria-label="Flat illustration of a team reviewing analytics charts on a big display" style="left:113px;top:526px;width:487px;height:326px;background:linear-gradient(135deg,#d9e2f2,#c6d3ec 60%,#ecd6de)"></div>
  <h3 class="feature-title" style="left:675px;top:536px;font-weight:400">Sed ut perspiciatis unde omnis iste<br>natus error sit voluptatem</h3>
  <p class="feature-text" style="left:678px;top:634px;width:405px">Nemo enim ipsam voluptatem quia voluptas sit aspernatur aut odit aut fugit, sed quia consequuntur magni dolores eos qui ratione vol uptatem sequi nescemo enim ipsam voluptatem quia voluptas sit aspernatur aut odit aut fugit, sed quia consequuntur</p>
  <a class="btn-outline" style="left:679px;top:778px;width:164px;height:56px">Learn More</a>
</section>

<section class="launch">
  <div class="device" role="img" aria-label="Smartphone showing the product start screen"></div>
  <div class="launch-kicker">Health Benefits Plan</div>
  <div class="launch-title">Decisioneering Tool Launch</div>
  <p class="launch-text">Nemo enim ipsam voluptatem quia voluptas sit aspernatur aut odit aut fugit, sed quia consequuntur magni dolores eos qui ratione voluptatem sequi nesciunt. Neque porro quisquam est, qui dolorem ipsum quia dolor sit amet, consectetur, adipisci velit, sed quia non numquam eius modi tempora dolore magnam aliquam quaerat voluptatem.</p>
  <a class="btn-outline">Read More</a>
</section>

<h2 class="section-title" style="top:2980px;font-size:44px;font-weight:400">Contact <em>Us</em></h2>
<div class="rule" style="top:3049px"></div>
<form>
  <div class="field" style="left:280px;top:3090px;width:314px;height:46px">First Name :</div>
  <div class="field" style="left:604px;top:3090px;width:314px;height:46px">Last Name :</div>
  <div class="field" style="left:280px;top:3146px;width:314px;height:46px">Email :</div>
  <div class="field" style="left:604px;top:3146px;width:314px;height:46px">Phone :</div>
  <div class="field" style="left:280px;top:3201px;width:638px;height:88px">Message :</div>
  <a class="btn-solid submit">SUBMIT</a>
</form>

<footer class="site-footer">
  <div class="footer-brand">Veltra Metrics</div>
  <nav class="footer-nav"><span>HOME</span>|<span>ABOUT US</span>|<span>PRODUCT</span>|<span>CONTACT US</span></nav>
  <div class="social" aria-label="Social links"><i></i><i></i><i></i><i></i><i></i></div>
  <div class="copyright">©2020 Veltra Metrics.All rights reserved.</div>
</footer>

</body>
</html>
```